Home Remodeling company needs a business card design

we need a business card design for home remodeling company in hamilton county, indiana USA. we offers a wide range of construction services including whole house renovations, Design and Build Basements and Kitchen and Bathroom Remodeling . we would like to see designs for both site of business card that use the same color of the company logo and also including all information below :
1- Karim Feltous CEO / General Contractor
2- all company contacts Telephone numbers ( 1-888-DULOM-47 ) ( 317-555-0193) email address ( info@dulomhome.com) website ( www.dulomhome.com ) and social media logos (Facebook- twitter- google plus )
3- company logo
4- licensed . insured . bonded

```html
<!DOCTYPE html>
<html lang="en">
<head>
<meta charset="utf-8">
<title>Dulom Home Remodeling – Business Card</title>
<link rel="stylesheet" href="https://fonts.googleapis.com/css2?family=Open+Sans:wght@400;600;700&display=swap">
<style>
  :root {
    --stage: #000000;
    --card: #333437;
    --brand-grey: #c9c9cb;
    --accent-red: #d2303a;
    --text-white: #f2f2f2;
    --rule: #8d8e91;
  }
  * { margin: 0; padding: 0; box-sizing: border-box; }
  html, body {
    width: 1200px; height: 900px; overflow: hidden;
    background: var(--stage);
    font-family: "Open Sans", sans-serif;
  }
  .stage { position: relative; width: 1200px; height: 900px; }
  .card {
    position: absolute; top: 271px; width: 456px; height: 281px;
    background: var(--card); border-radius: 14px; overflow: hidden;
  }
  .card--front { left: 137px; }
  .card--back { left: 627px; }

  .brand { position: absolute; color: var(--brand-grey); font-weight: 600; line-height: 1; }
  .brand__mark { position: absolute; background: var(--accent-red); }
  .brand__name { position: absolute; white-space: nowrap; }
  .brand__tagline { position: absolute; white-space: nowrap; }

  .card--front .brand { left: 35px; top: 30px; }
  .card--front .brand__mark { left: 0; top: 4px; width: 12px; height: 12px; }
  .card--front .brand__name { left: 16px; top: -4px; font-size: 42px; letter-spacing: 4px; }
  .card--front .brand__tagline { left: 16px; top: 39px; font-size: 13.5px; letter-spacing: 4.3px; }

  .card--back .brand { left: 90px; top: 108px; }
  .card--back .brand__mark { left: 0; top: 6px; width: 14px; height: 14px; }
  .card--back .brand__name { left: 18px; top: -6px; font-size: 50px; letter-spacing: 5px; }
  .card--back .brand__tagline { left: 18px; top: 47px; font-size: 16px; letter-spacing: 5.3px; }

  .person { position: absolute; left: 286px; top: 95px; }
  .person__name { color: var(--accent-red); font-size: 15px; font-weight: 600; line-height: 20px; }
  .person__title { color: var(--text-white); font-size: 12.5px; line-height: 18px; }

  .contacts { position: absolute; left: 289px; top: 157px; list-style: none; }
  .contacts__item {
    display: flex; align-items: center; gap: 6px;
    color: var(--text-white); font-size: 12.5px; line-height: 19px;
  }
  .contacts__icon { width: 10px; height: 10px; fill: var(--accent-red); flex: none; }

  .social { position: absolute; left: 289px; top: 245px; display: flex; gap: 8px; }
  .social__dot { width: 15px; height: 15px; border-radius: 50%; background: var(--text-white); }

  .credentials {
    position: absolute; left: 0; right: 0; top: 230px;
    display: flex; align-items: center; gap: 8px;
  }
  .credentials__rule { flex: 1; height: 1px; background: var(--rule); }
  .credentials__text { color: var(--text-white); font-size: 15.5px; font-weight: 600; white-space: nowrap; }
</style>
</head>
<body>
<main class="stage">
  <section class="card card--front">
    <div class="brand">
      <span class="brand__mark"></span>
      <span class="brand__name">DULOM</span>
      <span class="brand__tagline">HOME REMODELING</span>
    </div>
    <div class="person">
      <p class="person__name">Karim Feltous</p>
      <p class="person__title">CEO / General Contractor</p>
    </div>
    <ul class="contacts">
      <li class="contacts__item">
        <svg class="contacts__icon" viewBox="0 0 10 10"><path d="M2 0.5l1.6 2.2-1 1c.6 1.3 1.5 2.2 2.7 2.7l1-1L8.6 7 8 9c-4 0-7-3-7-7z"/></svg>
        1-888-DULOM-47
      </li>
      <li class="contacts__item">
        <svg class="contacts__icon" viewBox="0 0 10 10"><path d="M2 0.5l1.6 2.2-1 1c.6 1.3 1.5 2.2 2.7 2.7l1-1L8.6 7 8 9c-4 0-7-3-7-7z"/></svg>
        317-555-0193
      </li>
      <li class="contacts__item">
        <svg class="contacts__icon" viewBox="0 0 10 10"><path d="M0.5 2h9v6h-9z M0.5 2l4.5 3.5L9.5 2" stroke="#333437" stroke-width="0.8"/></svg>
        info@dulomhome.com
      </li>
      <li class="contacts__item">
        <svg class="contacts__icon" viewBox="0 0 10 10"><path d="M4 6l2-2" stroke="#d2303a" stroke-width="1.2" fill="none"/><path d="M5.5 2.5l1-1a1.8 1.8 0 0 1 2.5 2.5l-1 1M4.5 7.5l-1 1A1.8 1.8 0 0 1 1 6l1-1" stroke="#d2303a" stroke-width="1.2" fill="none"/></svg>
        www.dulomhome.com
      </li>
    </ul>
    <div class="social" aria-label="Social media">
      <span class="social__dot"></span>
      <span class="social__dot"></span>
      <span class="social__dot"></span>
    </div>
  </section>

  <section class="card card--back">
    <div class="brand">
      <span class="brand__mark"></span>
      <span class="brand__name">DULOM</span>
      <span class="brand__tagline">HOME REMODELING</span>
    </div>
    <div class="credentials">
      <span class="credentials__rule"></span>
      <span class="credentials__text">Licensed . Insured . Bonded</span>
      <span class="credentials__rule"></span>
    </div>
  </section>
</main>
</body>
</html>
```